Financial Advisor Resource Firm needs business card design

Need business card design for company in Omaha NE called Meridale Circle. We provide resources to financial advisors....workshop programs, retirement analysis, and insurance planning. I would like to see designs that use grays, greens, black, and white colors. The final design should communicate 'collaboration' and be simple yet attractive to financial planning clients. I will attached our logo and another picture of a puzzle piece coming together. I would like the incorporate the puzzle picture somehow, maybe on the back somehow, with color or just the gray scale....OR, the picture be the front of the card with 'Meridale' definition on it (see upload) and then company logo, employee name, title, address on the back (see ppt uploaded). The following disclosure needs to be included somewhere- Advisory services offered through Stonebrook Assets, LLC.
Updates

I uploaded a svg and ai file of the logo

Target Market(s)

Financial planning clients and financial advisors....so pretty diverse age range of about 40-70.

Industry/Entity Type

Financial Planning

Contact Information for Business Card

Tobias L. Fenwright, MBA
Founder/President
5287 E. Larkin Road
Suite 230
Omaha, NE 68190
Phone- (402) 555-0147
Cell- (402) 555-0183
Fax- (402) 555-0129
email- tobias@meridaleplan.example
web address- www.meridaleplan.example

Colors
1b1b1b
474747
d3d3d3
ffffff
9bcb3c
abd036

Requirements
Must have
• Must include logo provided, must be 2 sided, and must have disclosure...all of these items listed in project description

```html
<!DOCTYPE html>
<html lang="en">
<head>
<meta charset="utf-8">
<title>Meridale Circle – Business Card</title>
<link rel="stylesheet" href="https://fonts.googleapis.com/css2?family=Montserrat:wght@400;500;600;700&display=swap">
<style>
  :root {
    --ink: #1b1b1b;
    --black: #0b0b0c;
    --charcoal: #474747;
    --silver: #d3d3d3;
    --white: #ffffff;
    --green: #8cc63f;
    --stage: #4b4f55;
  }
  * { box-sizing: border-box; margin: 0; padding: 0; }
  html, body {
    width: 1200px; height: 1200px; overflow: hidden;
    background: var(--stage);
    font-family: "Montserrat", Arial, sans-serif;
  }
  .sheet {
    width: 1200px; height: 1200px;
    display: flex; flex-direction: column; align-items: center; justify-content: center;
    gap: 60px;
  }
  .card {
    position: relative;
    width: 840px; height: 490px;
    overflow: hidden;
    box-shadow: 0 14px 30px rgba(0,0,0,.35);
  }

  /* Back side */
  .card--back { background: var(--black); }
  .card__photo {
    position: absolute; inset: 0;
    background:
      radial-gradient(ellipse at 70% 45%, rgba(120,120,120,.35), transparent 60%),
      radial-gradient(ellipse at 20% 25%, rgba(90,90,90,.4), transparent 55%),
      linear-gradient(160deg, #2c2c2e 0%, #1a1a1b 55%, #0e0e0f 100%);
  }
  .back__brand {
    position: absolute; left: 0; right: 0; top: 206px;
    text-align: center; line-height: 1.2;
    color: var(--white);
    font-weight: 500; font-size: 58px; letter-spacing: 1px;
  }
  .back__web {
    position: absolute; left: 0; right: 0; top: 362px;
    text-align: center;
    color: var(--green);
    font-size: 19px; letter-spacing: 6px;
  }

  /* Front side */
  .card--front { background: var(--white); }
  .card__art { position: absolute; inset: 0; }
  .front__brand {
    position: absolute; left: 0; right: 0; top: 60px;
    text-align: center; line-height: 1.2;
    color: var(--ink);
    font-weight: 500; font-size: 40px; letter-spacing: .5px;
  }
  .front__brand-dot {
    display: inline-block; width: 18px; height: 18px; border-radius: 50%;
    background: var(--green); margin-right: 12px; vertical-align: 4px;
  }
  .front__info {
    position: absolute; left: 0; right: 0; top: 244px;
    text-align: center; color: var(--white);
  }
  .front__name { color: var(--green); font-weight: 700; font-size: 28px; line-height: 1.2; }
  .front__title { font-size: 21px; line-height: 1.2; margin-top: 2px; }
  .front__address { font-size: 16px; line-height: 1.2; margin-top: 46px; }
  .front__lines {
    display: flex; justify-content: center; gap: 24px;
    font-size: 16px; line-height: 1.2; margin-top: 12px;
  }
  .front__lines span, .front__email { display: inline-flex; align-items: center; gap: 6px; }
  .front__email { font-size: 16px; line-height: 1.2; margin-top: 12px; }
  .icon { width: 15px; height: 15px; fill: var(--green); }
  .front__disclosure {
    position: absolute; left: 0; right: 0; bottom: 14px;
    text-align: center; color: var(--silver);
    font-size: 11px; letter-spacing: .3px;
  }
</style>
</head>
<body>
<main class="sheet">

  <section class="card card--back">
    <div class="card__photo" role="img" aria-label="Grayscale photograph of hands fitting puzzle pieces together"></div>
    <div class="back__brand">Meridale Circle</div>
    <div class="back__web">www.meridaleplan.example</div>
  </section>

  <section class="card card--front">
    <svg class="card__art" viewBox="0 0 840 490" width="840" height="490" aria-hidden="true">
      <path d="M0,490 V410 C110,275 290,185 480,185 C640,185 770,285 840,378 V490 Z" fill="var(--black)"/>
      <path d="M0,341 C150,215 340,145 510,148 C650,152 770,210 840,263 L840,272 C760,225 640,172 500,170 C320,168 140,262 0,392 Z" fill="var(--green)"/>
    </svg>

    <div class="front__brand"><span class="front__brand-dot"></span>Meridale Circle</div>

    <div class="front__info">
      <div class="front__name">Tobias L. Fenwright, MBA</div>
      <div class="front__title">Founder/President</div>
      <div class="front__address">5287 E. Larkin Road, Suite 230 Omaha, NE 68190</div>
      <div class="front__lines">
        <span>
          <svg class="icon" viewBox="0 0 24 24"><path d="M6.6 10.8a15 15 0 0 0 6.6 6.6l2.2-2.2a1 1 0 0 1 1-.25 11.4 11.4 0 0 0 3.6.57 1 1 0 0 1 1 1V20a1 1 0 0 1-1 1A17 17 0 0 1 3 4a1 1 0 0 1 1-1h3.5a1 1 0 0 1 1 1c0 1.25.2 2.45.57 3.57a1 1 0 0 1-.25 1Z"/></svg>
          : (402) 555-0147
        </span>
        <span>
          <svg class="icon" viewBox="0 0 24 24"><path d="M7 2h10a1 1 0 0 1 1 1v18a1 1 0 0 1-1 1H7a1 1 0 0 1-1-1V3a1 1 0 0 1 1-1Zm1 3v13h8V5Zm4 14.2a1 1 0 1 0 0 2 1 1 0 0 0 0-2Z"/></svg>
          : (402) 555-0183
        </span>
        <span>
          <svg class="icon" viewBox="0 0 24 24"><path d="M7 3h10v5H7Zm-3 6h16a2 2 0 0 1 2 2v6h-4v4H6v-4H2v-6a2 2 0 0 1 2-2Zm4 7v3h8v-3Z"/></svg>
          : (402) 555-0129
        </span>
      </div>
      <div class="front__email">
        <svg class="icon" viewBox="0 0 24 24"><path d="M2 5h20v14H2Zm2 2v.5l8 5 8-5V7l-8 5Z"/></svg>
        : tobias@meridaleplan.example
      </div>
    </div>

    <p class="front__disclosure">Advisory services offered through Stonebrook Assets, LLC.</p>
  </section>

</main>
</body>
</html>
```